COMPANY NAME: Bright Harbor Ventures: Task Description: We are a new UK based business with global rea

Target Market

- Personal and professional development – 30-55 age group, corporate leaders, Eastern European and Asian markets
- On-assignment projects – Corporate market – Eastern European and Asian Markets
- Property investment - 35-65 age group, Europe, USA, Australia

What we need

We need logos and brand design for a suite of web platforms (website, twitter and Facebook profile). We would like to have a cohesive and consistent look across all of our online platforms. The design suite must therefore include social media logos, backgrounds and headers. Specifically we are looking for:

a. Facebook header/page design: likely to have a more youthful look

b. Website: Header, background and layout that is responsive to devices, iPhone primarily, then tablet, then PC (we have purchased a website building package from SiteKettle so if you are familiar with one of their themes, it would be great to have a design that fits with a theme you would recommend); Design should be able to accommodate a place to position video in the medium term but an image in the short term.

c. LinkedIn: header/logo; more corporate look

d. Twitter: background/logo

e. Powerpoint template: background and logo - simple and soft background not busy

f. Electronic Newsletter: logo, header and sidebar; simple and soft background not busy

h. Business card: sophisticated and simple

Colors

We have in mind a preference for colors from the purple family, maybe lavender, so as to appeal to all genders and age groups. Though we are happy to go with a recommendation if you think otherwise.

We would like a look that is professional, airy, bright, fresh, futuristic, insightful, friendly.

Ethos of the brand

- experiencing opportunity and being fulfilled in a changing world
- services are facilitated through insights
- support provided through our product, services and tailored approach to coaching/partnerships (which includes private client match-making)
- we are service providers and passionate about quality and modern leadership skills at all stages in life.

The company name is "Bright Harbor Ventures” - our main message is helping people move to the next level - through investments, personal and professional growth.

Some of our messaging

1. International Leadership in a new world.

2. New technology;

3. Informed;

4. Positively Influential

5. Making a difference;

6. Empowered;

7. Risk free investments;

8. Commercial opportunity;

9. Fulfilled living;

10. Carefree and Fun Living;

11. Progression;

12. Open-minded

13. Energy/dynamic

The Business:
The business is to move people very quickly out of situations that hold them back. the situations could be their own personal situations; their career; their jobs; their teams; their ideas; their finances; their financial opportunities. Remove their fears and give them the strategies to take action. The team are international and have 40 years experience between them in this area.

We do want to come across modern and dynamic, customer outcome focussed, building long-term relationships; international.
Updates

Project Deadline Extended
Reason: We have not found the right designs - we are not just looking for a website design but also images and logos. Most images we can see in the designs are stock images - very standard. We need an image which will be the face of the company, like the shop front window. This main image will be used on social media (top image) and also the home page of the website.

Target Market(s)

30-55 years
Eastern Europe; UK; Asia; Africa; Middle East
Personal, Professional, Corporate, and Financial Growth

Industry/Entity Type

Business Service

Contact Information for Business Card

Simple and stylish
the 3 areas of the business on the reverse -

International look - Offices in UK and San Francisco

Company name
web address www.brightharborventure.com
email director@brightharborventure.com
Facebook bright harbor venture
LinkedIn Bright Harbor Venture
Twitter Bright Harbor Venture
Telephone: +44 (0) 768 213 5597

Logo Text

Something that symbolises unlimited growth - probably not text - could use the word INSIGHT in some way

Number of Pages Required

1 page

Colors
e4daeb
f3f1f8
ffffff

Requirements
Must have
• social media symbols and address
• company name
• Melanie Thorpe
• Director
• Telephone +44 (0) 768 213 5597
• Website name www.brightharborventure.co.uk
• Reverse of Card:
• Discreet, Fast, Bright Harbor Consultancy
• Corporate, Professional, Personal & Property Investment
Nice to have
• not too angular; soft lines; not too cluttered (possibly social media on the reverse and just logo, name, number on the front?
Should not have
• too busy

```html
<!DOCTYPE html>
<html lang="en">
<head>
<meta charset="utf-8">
<title>Bright Harbor Venture — Consulting</title>
<link rel="stylesheet" href="https://fonts.googleapis.com/css2?family=Montserrat:wght@400;500;600;700&family=Open+Sans:ital,wght@0,400;0,600;1,400&display=swap">
<style>
:root{
  --ink:#222222;
  --ink-soft:#555555;
  --muted:#777777;
  --white:#ffffff;
  --mist:#eeedf3;
  --panel:#232323;
  --footer:#232323;
  --footer-base:#1b1b1b;
  --button-top:#3a3a3a;
  --button-bottom:#151515;
  --line:#dddddd;
  --head:'Montserrat',Arial,sans-serif;
  --body:'Open Sans',Arial,sans-serif;
}
*{box-sizing:border-box;margin:0;padding:0}
html,body{width:1200px;height:2899px;overflow:hidden}
body{position:relative;background:var(--white);font-family:var(--body);color:var(--ink)}
.abs{position:absolute}
.btn{position:absolute;display:flex;align-items:center;justify-content:center;color:var(--white);font-family:var(--body);font-size:11px;font-weight:600;letter-spacing:.3px;background:linear-gradient(var(--button-top),var(--button-bottom));border-radius:3px}
.section-title{position:absolute;left:0;width:1200px;text-align:center;font-family:var(--head);font-weight:500;font-size:31px;color:var(--ink);letter-spacing:.2px}

/* header */
.site-header{position:absolute;left:0;top:0;width:1200px;height:128px;border-top:4px solid #333;background:var(--white)}
.brand{left:131px;top:50px;font-family:var(--head);font-size:28px;font-weight:500;color:#333;letter-spacing:.4px}
.contact-chip{top:24px;display:flex;align-items:center;gap:14px;font-size:12px;font-weight:600;color:#333}
.contact-chip svg{width:28px;height:28px}
.main-nav{top:88px;left:508px;display:flex;gap:0}
.main-nav a{position:absolute;top:0;white-space:nowrap;font-family:var(--head);font-size:11.5px;font-weight:500;color:#888;text-decoration:none}
.main-nav a.active{color:#222}
.nav-underline{left:504px;top:124px;width:40px;height:4px;background:#333}

/* hero */
.hero{left:0;top:128px;width:1200px;height:425px;background:linear-gradient(180deg,#6b5c4e 0%,#4f4a47 35%,#3f4247 65%,#5d5048 100%)}
.hero-shade{left:0;top:128px;width:1200px;height:425px;background:rgba(20,20,25,.35)}
.hero-title{left:0;top:230px;width:1200px;text-align:center;font-family:var(--head);font-weight:700;font-size:47px;color:var(--white);letter-spacing:.5px}
.hero-sub{left:0;top:318px;width:1200px;text-align:center;font-size:16px;color:#eee}
.dots{top:496px;left:572px;display:flex;gap:10px}
.dots span{width:12px;height:12px;border-radius:50%;background:var(--white)}
.dots span.on{background:transparent;border:2px solid var(--white)}

/* welcome */
.welcome-text{left:131px;top:660px;width:937px;text-align:center;font-size:11px;line-height:19px;color:var(--ink-soft)}

/* services */
.services{left:0;top:852px;width:1200px;height:497px;background:var(--mist)}
.service{position:absolute;top:980px;width:300px;text-align:center}
.service svg{display:block;margin:0 auto;width:90px;height:90px}
.service h3{margin-top:37px;font-family:var(--head);font-weight:500;font-size:19px;color:var(--ink);letter-spacing:.3px}
.service p{margin:22px auto 0;width:225px;font-size:11px;line-height:19px;color:var(--ink-soft)}

/* values */
.values-photo{left:0;top:1349px;width:601px;height:405px;background:linear-gradient(110deg,#3a4a5c 0%,#c9c4c2 35%,#efe8e4 55%,#6f7c8c 80%,#2e3440 100%)}
.values-panel{left:601px;top:1349px;width:599px;height:405px;background:var(--panel)}
.values-title{left:653px;top:1400px;font-family:var(--head);font-weight:500;font-size:29px;color:var(--white)}
.values-text{left:653px;width:414px;font-size:11px;line-height:20px;color:#e6e6e6}
.btn-outline{position:absolute;left:653px;top:1663px;width:86px;height:34px;border:1px solid #ccc;border-radius:3px;color:var(--white);font-size:11px;font-weight:600;display:flex;align-items:center;justify-content:center}

/* testimonials */
.testimonials{left:0;top:1754px;width:1200px;height:363px;background:linear-gradient(135deg,#4a5058 0%,#2b3038 40%,#1e2228 70%,#3c424b 100%)}
.testimonials-shade{left:0;top:1754px;width:1200px;height:363px;background:rgba(10,12,16,.35)}
.testi-title{left:0;top:1826px;width:1200px;text-align:center;font-family:var(--head);font-weight:500;font-size:31px;color:var(--white)}
.testi-quote{left:131px;top:1897px;width:937px;text-align:center;font-size:11.5px;line-height:25px;color:#eee}
.testi-name{left:0;top:1965px;width:1200px;text-align:center;font-size:13px;font-style:italic;color:#ddd}
.arrows{left:572px;top:2027px;display:flex;gap:8px}
.arrows span{width:24px;height:26px;border:1px solid #ddd;display:flex;align-items:center;justify-content:center}

/* blog */
.post{position:absolute;top:2260px;width:296px}
.post-photo{width:296px;height:151px}
.post h3{margin-top:28px;font-family:var(--head);font-weight:500;font-size:20px;color:var(--ink)}
.post time{display:block;margin-top:4px;font-size:11px;color:#444}
.post p{margin-top:12px;font-size:11px;line-height:20px;color:#444}

/* footer */
.site-footer{left:0;top:2575px;width:1200px;height:259px;background:var(--footer)}
.footer-base{left:0;top:2834px;width:1200px;height:65px;background:var(--footer-base);color:#ccc;font-size:11px;display:flex;align-items:center;justify-content:center}
.footer-title{top:2622px;font-family:var(--head);font-weight:500;font-size:19px;color:var(--white);letter-spacing:.3px}
.footer-text{font-size:11.5px;line-height:20px;color:#e6e6e6}
.footer-row{position:absolute;left:131px;display:flex;gap:16px;font-size:11.5px;color:#e6e6e6;line-height:20px}
.footer-row svg{width:12px;height:12px;margin-top:4px;flex:none}
.quick-links{left:419px;top:2664px;list-style:none}
.quick-links li{font-size:11.5px;line-height:20.2px;color:#e6e6e6}
.newsletter-input{left:622px;top:2718px;width:228px;height:36px;background:#4a4a4a;display:flex;align-items:center;justify-content:space-between;padding:0 14px;font-size:11.5px;color:#ddd}
.social{top:2667px;left:927px;display:flex;gap:8px}
.social span{width:40px;height:40px;border-radius:50%;background:#555}
</style>
</head>
<body>

<header class="site-header">
  <div class="abs brand">BRIGHT HARBOR VENTURE</div>
  <div class="abs contact-chip" style="left:765px">
    <svg viewBox="0 0 28 28"><circle cx="14" cy="14" r="12.5" fill="none" stroke="#333" stroke-width="1.5"/><path d="M10 8.5l2.2-.5 1.3 3-1.5 1.2a7 7 0 0 0 3.8 3.8l1.2-1.5 3 1.3-.5 2.2c-5.6.3-9.8-3.9-9.5-9.5z" fill="#333"/></svg>
    <span>1800-555-0187</span>
  </div>
  <div class="abs contact-chip" style="left:905px">
    <svg viewBox="0 0 28 28"><circle cx="14" cy="14" r="12.5" fill="none" stroke="#333" stroke-width="1.5"/><rect x="8.5" y="10" width="11" height="8" fill="none" stroke="#333" stroke-width="1.4"/><path d="M8.5 10l5.5 4.5 5.5-4.5" fill="none" stroke="#333" stroke-width="1.4"/></svg>
    <span>hello@brightharborventure.com</span>
  </div>
  <nav class="abs main-nav">
    <a class="active" style="left:0">HOME</a>
    <a style="left:81px">ABOUT US</a>
    <a style="left:184px">OUR VALUES</a>
    <a style="left:302px">TESTIMONIALS</a>
    <a style="left:427px">NEWS</a>
    <a style="left:504px">CONTACT</a>
  </nav>
  <div class="abs nav-underline"></div>
</header>

<section>
  <div class="abs hero" role="img" aria-label="Aerial photograph of a river city skyline at dusk"></div>
  <div class="abs hero-shade"></div>
  <h1 class="abs hero-title">WE ARE A CONSULTING COMPANY</h1>
  <p class="abs hero-sub">Lorem ipsum dolor sit amet, consectetur adipiscing elit</p>
  <div class="btn" style="left:535px;top:384px;width:132px;height:45px">VIEW DETAILS</div>
  <div class="abs dots"><span class="on"></span><span></span><span></span></div>
</section>

<section>
  <h2 class="section-title" style="top:600px">WELCOME TO BRIGHT HARBOR VENTURE</h2>
  <p class="abs welcome-text">If you seek an experienced and trusted partner to work with you on an assignment or simply want some strategies to move your personal or professional talents to the next level then you are in the right place.&nbsp; If you feel that the pace of change in business is so fast that to be an outstanding leader you should ensure you are brought up to speed regularly then you are in the right place.If you are hearing about the essential new leadership essentials and you are ready to hear how to adopt them</p>
  <div class="btn" style="left:545px;top:738px;width:110px;height:37px">READ MORE</div>
</section>

<section>
  <div class="abs services"></div>
  <h2 class="section-title" style="top:903px">OUR SERVICES</h2>

  <div class="service" style="left:103px">
    <svg viewBox="0 0 90 90"><rect x="19" y="19" width="52" height="52" transform="rotate(45 45 45)" fill="#222"/><rect x="36" y="36" width="18" height="16" fill="none" stroke="#fff" stroke-width="1.6"/><path d="M40 50v-5M44 50v-8M48 50v-6M52 50v-10" stroke="#fff" stroke-width="2"/></svg>
    <h3>CONSULTANCY</h3>
    <p>If you are hearing about the essential new leadership essentials and you are ready to hear how to adopt</p>
    <div class="btn" style="left:95px;top:247px;width:110px;height:37px">READ MORE</div>
  </div>

  <div class="service" style="left:449px">
    <svg viewBox="0 0 90 90"><rect x="19" y="19" width="52" height="52" transform="rotate(45 45 45)" fill="#fff" stroke="#333" stroke-width="1.2"/><rect x="36" y="39" width="18" height="13" rx="1.5" fill="#333"/><rect x="41" y="35.5" width="8" height="4" fill="none" stroke="#333" stroke-width="1.6"/><path d="M36 45h18" stroke="#fff" stroke-width="1"/></svg>
    <h3>ON ASSIGNMENT</h3>
    <p>If you are hearing about the essential new leadership essentials and you are ready to hear how to adopt</p>
    <div class="btn" style="left:95px;top:247px;width:110px;height:37px">READ MORE</div>
  </div>

  <div class="service" style="left:804px">
    <svg viewBox="0 0 90 90"><rect x="19" y="19" width="52" height="52" transform="rotate(45 45 45)" fill="#fff" stroke="#333" stroke-width="1.2"/><circle cx="45" cy="40" r="5" fill="#333"/><path d="M35 55c0-6 4.5-9 10-9s10 3 10 9z" fill="#333"/></svg>
    <h3>PRIVATE CLIENT</h3>
    <p>If you are hearing about the essential new leadership essentials and you are ready to hear how to adopt</p>
    <div class="btn" style="left:95px;top:247px;width:110px;height:37px">READ MORE</div>
  </div>
</section>

<section>
  <div class="abs values-photo" role="img" aria-label="Photograph of a business team seated around a meeting table"></div>
  <div class="abs values-panel"></div>
  <h2 class="abs values-title">OUR VALUES</h2>
  <p class="abs values-text" style="top:1461px">If you seek an experienced and trusted partner to work with you on an assignment or simply want some strategies to move your personal or professional talents to the next level then you are in the right place.</p>
  <p class="abs values-text" style="top:1538px">If you feel that the pace of change in business is so fast that to be an outstanding leader you should ensure you are brought up to speed regularly then you are in the right place.If you are hearing about the essential new leadership essentials and you are ready to hear how to adopt them into your life or business then you are at the right place.</p>
  <div class="btn-outline">READ MORE</div>
</section>

<section>
  <div class="abs testimonials" role="img" aria-label="Photograph looking up at glass office towers"></div>
  <div class="abs testimonials-shade"></div>
  <h2 class="abs testi-title">TESTIMONIALS</h2>
  <p class="abs testi-quote">Lorem ipsum dolor sit amet, consectetur adipiscing elit, sed do eiusmod tempor incididunt ut labore et dolore magna aliqua. Ut enim ad minim veniam, quis nostrud exercitation ulla-<br>mco laboris nisi ut aliquip ex ea commodo consequat</p>
  <p class="abs testi-name">Clara Wendt -</p>
  <div class="abs arrows">
    <span><svg width="8" height="10" viewBox="0 0 8 10"><path d="M6 1L2 5l4 4" fill="none" stroke="#fff" stroke-width="1.5"/></svg></span>
    <span><svg width="8" height="10" viewBox="0 0 8 10"><path d="M2 1l4 4-4 4" fill="none" stroke="#fff" stroke-width="1.5"/></svg></span>
  </div>
</section>

<section>
  <h2 class="section-title" style="top:2182px">FROM THE BLOG</h2>
  <article class="post" style="left:131px">
    <div class="post-photo" role="img" aria-label="Photograph of a man overlooking a misty city from a rooftop" style="background:linear-gradient(180deg,#cfd3d6,#8a9096 60%,#4d5358)"></div>
    <h3>LOREM IPSUM</h3><time>SEP 26,2016</time>
    <p>Neque porro quisquam est qui dolorem ipsum quia dolor sit amet, consectetur, adipisci velit...</p>
  </article>
  <article class="post" style="left:452px">
    <div class="post-photo" role="img" aria-label="Photograph of a businessman in a suit in an office" style="background:linear-gradient(135deg,#2f5f8f,#7fa3c4 50%,#1f3550)"></div>
    <h3>LOREM IPSUM</h3><time>SEP 26,2016</time>
    <p>Neque porro quisquam est qui dolorem ipsum quia dolor sit amet, consectetur, adipisci velit...</p>
  </article>
  <article class="post" style="left:771px">
    <div class="post-photo" role="img" aria-label="Photograph of a businesswoman working at a bright desk" style="background:linear-gradient(135deg,#f2ede6,#d8c7b3 50%,#b9a48e)"></div>
    <h3>LOREM IPSUM</h3><time>SEP 26,2016</time>
    <p>Neque porro quisquam est qui dolorem ipsum quia dolor sit amet, consectetur, adipisci velit...</p>
  </article>
</section>

<footer>
  <div class="abs site-footer"></div>

  <h4 class="abs footer-title" style="left:131px">CONTACT US</h4>
  <div class="footer-row" style="top:2664px">
    <svg viewBox="0 0 12 12"><path d="M6 .5a3.8 3.8 0 0 0-3.8 3.8C2.2 7 6 11.5 6 11.5s3.8-4.5 3.8-7.2A3.8 3.8 0 0 0 6 .5z" fill="#e6e6e6"/><circle cx="6" cy="4.3" r="1.4" fill="#232323"/></svg>
    <span>$2868 Lorem ipsum dolor sit amet,<br>consectetur adipiscing elit</span>
  </div>
  <div class="footer-row" style="top:2724px">
    <svg viewBox="0 0 12 12"><path d="M2 1.5l2-.5 1.2 2.8-1.3 1a5.5 5.5 0 0 0 3.3 3.3l1-1.3L11 8l-.5 2C5.4 10.4 1.6 6.6 2 1.5z" fill="#e6e6e6"/></svg>
    <span>1800-555-0142</span>
  </div>
  <div class="footer-row" style="top:2744px">
    <svg viewBox="0 0 12 12"><rect x="1" y="2.5" width="10" height="7" fill="none" stroke="#e6e6e6" stroke-width="1.2"/><path d="M1 2.5l5 4 5-4" fill="none" stroke="#e6e6e6" stroke-width="1.2"/></svg>
    <span>hello@brightharborventure.com</span>
  </div>

  <h4 class="abs footer-title" style="left:419px">QUICK LINKS</h4>
  <ul class="abs quick-links">
    <li>Home</li><li>About Us</li><li>Our Values</li><li>Testimonials</li><li>News</li><li>Contact</li>
  </ul>

  <h4 class="abs footer-title" style="left:622px">NEWSLETTER</h4>
  <p class="abs footer-text" style="left:622px;top:2664px;width:240px">Subscribe newsletter to receive the updates direct to your inbox.</p>
  <div class="abs newsletter-input"><span>Email Id</span>
    <svg width="14" height="14" viewBox="0 0 14 14"><path d="M1 7l12-6-4 12-2.5-4.5z" fill="#fff"/></svg>
  </div>

  <h4 class="abs footer-title" style="left:927px">FOLLOW US</h4>
  <div class="abs social" aria-label="Social media links"><span></span><span></span><span></span></div>

  <div class="abs footer-base">© 2016 Bright Harbor Venture. All rights reserved.</div>
</footer>

</body>
</html>
```